Veterinary Pylon

My veterinary clinic is not clearly visible from the street and I want to place a Pylon next to my driveway. I want a modern, elegant straight Design, the Photo shows the sheduled place. One can see the clinic on our Homepage: www.tailbright-vethaus.at
The last pictures are examples for pylones I like

Target Market(s)

the passing cars often miss my entry...I want to show where to turn left

Colors
3276b5
33a6d7
00a990

Requirements
Must have
• High value, simple elegance, size: 250cm (high) x 100cm (width)
Nice to have
• Our Logo, arrow(?)

A special Text is not necessary but this will be an option:

Biegen sie hier ab und wir biegen es wieder hin!
Should not have
• Too much Color, the colors I have chosen are the possible colors but it‘s not necessary to use them.

```html
<!DOCTYPE html>
<html lang="de">
<head>
<meta charset="utf-8">
<title>Tailbright Vethaus – Pylon</title>
<link href="https://fonts.googleapis.com/css2?family=Archivo+Black&display=swap" rel="stylesheet">
<style>
  :root {
    --navy: #114a93;
    --cyan: #2fbbdf;
    --mist: #eef2f8;
    --white: #ffffff;
  }
  html, body {
    margin: 0;
    padding: 0;
    width: 1200px;
    height: 3000px;
    overflow: hidden;
    background: var(--white);
  }
  .pylon {
    position: relative;
    width: 1200px;
    height: 3000px;
    overflow: hidden;
    background: var(--white);
  }
  .pylon__halo {
    position: absolute;
    left: 0;
    top: 0;
    width: 1200px;
    height: 1600px;
  }
  .brand {
    position: absolute;
    left: 0;
    top: 420px;
    width: 1200px;
    text-align: center;
    font-family: "Archivo Black", sans-serif;
    font-weight: 400;
    color: var(--navy);
    letter-spacing: 0.04em;
    line-height: 1.05;
  }
  .brand__line {
    display: block;
  }
  .brand__line--main {
    font-size: 138px;
  }
  .brand__line--sub {
    font-size: 118px;
    letter-spacing: 0.14em;
  }
  .direction-sign {
    position: absolute;
    left: 413px;
    top: 1330px;
    width: 434px;
    height: 434px;
  }
  .pylon__base {
    position: absolute;
    left: 0;
    top: 2100px;
    width: 1200px;
    height: 900px;
  }
</style>
</head>
<body>
<main class="pylon">
  <svg class="pylon__halo" viewBox="0 0 1200 1600" aria-hidden="true">
    <defs>
      <linearGradient id="haloFade" x1="0" y1="0" x2="0" y2="1">
        <stop offset="0.35" stop-color="#ffffff"/>
        <stop offset="1" stop-color="#eef2f8"/>
      </linearGradient>
    </defs>
    <ellipse cx="600" cy="350" rx="1000" ry="1176" fill="url(#haloFade)"/>
  </svg>

  <h1 class="brand">
    <span class="brand__line brand__line--main">TAILBRIGHT</span>
    <span class="brand__line brand__line--sub">VETHAUS</span>
  </h1>

  <svg class="direction-sign" viewBox="0 0 434 434" role="img" aria-label="Hier links abbiegen">
    <defs>
      <linearGradient id="signFill" x1="0" y1="0" x2="1" y2="0">
        <stop offset="0" stop-color="#114a93"/>
        <stop offset="1" stop-color="#2fbbdf"/>
      </linearGradient>
    </defs>
    <circle cx="217" cy="217" r="217" fill="url(#signFill)"/>
    <g fill="none" stroke="#ffffff" stroke-width="21">
      <line x1="103" y1="217" x2="344" y2="217"/>
      <polyline points="189,128 101,217 189,306"/>
    </g>
  </svg>

  <svg class="pylon__base" viewBox="0 0 1200 900" aria-hidden="true">
    <path d="M0 27 C120 30 240 60 340 110 L0 380 Z" fill="var(--cyan)"/>
    <path d="M0 305 C280 90 560 20 770 27 C920 32 1060 60 1200 107 L1200 900 L0 900 Z" fill="var(--navy)"/>
  </svg>
</main>
</body>
</html>
```